Maplecrest Disability - Social Security Disability Attorneys

Our company is expanding to attract clients nationwide for our social security disability practice. We have a logo, but I am looking for a creative and elegant letterhead that projects an image of being technologically advanced but still professional enough for the legal field. I am looking for the "wow factor" combined with this is still professional enough for a law practice.

Requesting letterhead and business card design
Updates

Had to update and change the logo. The previous logo had a typo. Please send updates with the new logo for consideration. The letterhead and business cards should be professional enough to be used for a law firm. Thanks.

Industry/Entity Type

Law Practice, Law Firm, Healthcare Industry, Government

Colors

Designer to choose colors to be used in the design.

Requirements
Nice to have
• **Please create a vertical design for the business card**

```html
<!DOCTYPE html>
<html lang="en">
<head>
<meta charset="utf-8">
<title>Maplecrest Disability – Letterhead</title>
<link rel="stylesheet" href="https://fonts.googleapis.com/css2?family=Lato:wght@400;700&family=Italianno&display=swap">
<style>
  :root {
    --backdrop: #e4e4e6;
    --paper: #ffffff;
    --ink: #2f2f33;
    --ink-soft: #4a4a50;
    --brand-blue: #5471b6;
    --brand-orange: #f28a2a;
  }
  * { box-sizing: border-box; margin: 0; padding: 0; }
  html, body {
    width: 1200px; height: 960px; overflow: hidden;
    background: var(--backdrop);
    font-family: "Lato", Arial, sans-serif;
    color: var(--ink);
  }
  .letterhead {
    position: absolute; left: 282px; top: 30px;
    width: 636px; height: 900px;
    background: var(--paper);
    box-shadow: 0 6px 24px rgba(0,0,0,.12);
    overflow: hidden;
  }
  .brand {
    position: absolute; left: 52px; top: 92px;
    display: flex; align-items: center; gap: 10px;
    color: var(--brand-blue);
  }
  .brand-dot { width: 14px; height: 14px; border-radius: 50%; background: var(--brand-orange); }
  .brand-name { font-size: 19px; font-weight: 400; letter-spacing: 2px; text-transform: uppercase; line-height: 1; }
  .brand-tagline {
    position: absolute; left: 76px; top: 116px;
    font-size: 6.5px; letter-spacing: 2.2px; text-transform: uppercase; color: var(--brand-blue);
  }
  .contact {
    position: absolute; left: 392px; top: 46px;
    border-left: 1px solid var(--brand-orange);
    padding-left: 12px;
    font-size: 8.5px; line-height: 1.55; color: var(--ink);
  }
  .contact-row { display: flex; align-items: center; gap: 6px; }
  .contact-icon { width: 9px; height: 9px; flex: none; }
  .letter {
    position: absolute; left: 74px; top: 196px; width: 470px;
    font-size: 10.5px; line-height: 1.45; color: var(--ink-soft);
  }
  .letter-date { margin-bottom: 14px; font-size: 11.5px; }
  .recipient { margin-bottom: 14px; font-size: 11.5px; }
  .recipient p { margin-bottom: 0; }
  .recipient .gap { margin-top: 12px; }
  .salutation { font-size: 13.5px; font-weight: 700; color: var(--ink); margin-bottom: 12px; }
  .letter-body p { margin-bottom: 12px; }
  .closing { margin-top: 14px; font-size: 11px; }
  .signature {
    font-family: "Italianno", cursive;
    font-size: 52px; color: var(--ink); line-height: 1; margin-top: 6px; margin-left: 30px;
  }
  .wave { position: absolute; left: 0; bottom: 0; width: 636px; height: 320px; }
</style>
</head>
<body>
  <main class="letterhead">
    <header>
      <div class="brand">
        <span class="brand-dot"></span>
        <span class="brand-name">Maplecrest Disability</span>
      </div>
      <div class="brand-tagline">Social Security Disability Attorneys</div>

      <address class="contact" style="font-style:normal">
        <div>Suite 4, Level 12, Harbour Lane</div>
        <div>Northvale NSW 2100</div>
        <div class="contact-row">
          <svg class="contact-icon" viewBox="0 0 10 10"><circle cx="5" cy="5" r="5" fill="var(--brand-orange)"/><path d="M3 2.6c.4-.3.8-.2 1 .2l.4.8c.1.3 0 .5-.2.7l-.3.2c.3.7.8 1.2 1.5 1.5l.2-.3c.2-.2.4-.3.7-.2l.8.4c.4.2.5.6.2 1-.5.6-1.2.7-2 .3C4 6.6 3.3 5.9 2.9 5c-.4-.8-.4-1.8.1-2.4z" fill="#fff"/></svg>
          <span>555-204-7319</span>
        </div>
        <div class="contact-row">
          <svg class="contact-icon" viewBox="0 0 10 10"><rect x="0.5" y="2" width="9" height="6" rx="1" fill="var(--brand-orange)"/><path d="M1 2.6l4 3 4-3" stroke="#fff" stroke-width=".8" fill="none"/></svg>
          <span>info@maplecrestdisability.com</span>
        </div>
        <div class="contact-row">
          <svg class="contact-icon" viewBox="0 0 10 10"><circle cx="5" cy="5" r="4.6" fill="var(--brand-orange)"/><g stroke="#fff" stroke-width=".6" fill="none"><ellipse cx="5" cy="5" rx="1.8" ry="4"/><path d="M1 5h8M1.6 3h6.8M1.6 7h6.8"/></g></svg>
          <span>www.maplecrestdisability.com</span>
        </div>
      </address>
    </header>

    <article class="letter">
      <p class="letter-date">January-03-2020</p>
      <div class="recipient">
        <p>Mr. Alan Reed</p>
        <p>President</p>
        <p class="gap">Crestline Corporation</p>
        <p>48 Birchwood Avenue, Suite# 10</p>
        <p>City, State, 120023</p>
      </div>
      <p class="salutation">Dear Mr. Reed</p>
      <div class="letter-body">
        <p>Lorem ipsum dolor sit amet, consectetur adipisicing elit, sed do eiusmod tempor incididunt ut labore et dolore magna aliqua. Ut enim ad minim veniam, quis nostrud exercitation ullamco laboris nisi ut aliquip ex ea commodo consequat. Duis aute irure dolor in reprehenderit in voluptate velit esse cillum dolore eu fugiat nulla pariatur.</p>
        <p>Lorem ipsum dolor sit amet, consectetur adipisicing elit, sed do eiusmod tempor incididunt ut labore et dolore magna aliqua. Ut enim ad minim veniam, quis nostrud exercitation ullamco laboris nisi ut aliquip ex ea commodo consequat. Duis aute irure dolor in reprehenderit in voluptate velit esse cillum dolore eu fugiat nulla pariatur.</p>
        <p>Lorem ipsum dolor sit amet, consectetur adipisicing elit, sed do eiusmod tempor incididunt ut labore et dolore magna aliqua. Ut enim ad minim veniam, quis nostrud exercitation ullamco laboris nisi ut aliquip ex ea commodo consequat.</p>
        <p>Excepteur sint occaecat cupidatat non proident, sunt in culpa qui officia deserunt mollit anim id est laborum. re et dolore magnam aliquam quaerat voluptatem.</p>
      </div>
      <p class="closing">Regards</p>
      <p class="signature">Daniel Harper</p>
    </article>

    <svg class="wave" viewBox="0 0 636 320" preserveAspectRatio="none" aria-hidden="true">
      <path d="M0 320 L0 306 C110 292 200 290 300 250 C420 200 470 80 636 52 L636 320 Z" fill="var(--brand-blue)"/>
      <path d="M228 282 C340 262 400 196 456 136 C510 80 560 52 600 40 C560 58 516 90 466 146 C406 212 330 270 228 282 Z" fill="var(--brand-orange)"/>
    </svg>
  </main>
</body>
</html>
```